Health Care Company with Logo Needs Business Cards designed

We are a luxury behavioral health company looking for business cards design we already have a logo and are looking for someone to design a sophisticated luxurious looking business card. Please note that Card design should be captivating just like the logo and also encompass the logo color

Industry/Entity Type

Healthcare

Contact Information for Business Card

Logo,company name, tagline, my name and title, contact details, and physical address

```html
<!DOCTYPE html>
<html lang="en">
<head>
<meta charset="utf-8">
<title>Orrin Wellness Group – Business Cards</title>
<link href="https://fonts.googleapis.com/css2?family=Roboto:wght@400;500;700;900&display=swap" rel="stylesheet">
<style>
  :root {
    --backdrop: #3b3b3b;
    --card: #161616;
    --edge: #19a6ee;
    --brand-purple: #7d3fa6;
    --brand-blue: #19a6ee;
    --brand-orange: #f7941d;
    --brand-green: #8dc63f;
    --text-light: #f2f2f2;
  }
  * { box-sizing: border-box; margin: 0; padding: 0; }
  html, body { width: 1200px; height: 801px; overflow: hidden; }
  body {
    background: var(--backdrop);
    font-family: "Roboto", Arial, sans-serif;
    position: relative;
  }
  .card {
    position: absolute;
    width: 525px;
    height: 300px;
    background: var(--card);
    border-bottom: 3px solid var(--edge);
    box-shadow: 0 14px 30px rgba(0,0,0,.45);
  }
  .card--front { left: 50px; top: 250px; }
  .card--back { left: 625px; top: 250px; overflow: hidden; }

  .brand { position: absolute; left: 30px; top: 34px; display: flex; align-items: center; gap: 10px; }
  .brand__square { width: 22px; height: 22px; background: var(--brand-purple); }
  .brand__name { font-weight: 900; font-size: 25px; color: var(--brand-purple); letter-spacing: .2px; }
  .brand__tagline {
    position: absolute; left: 62px; top: 66px;
    font-size: 7.5px; font-weight: 700; letter-spacing: 1.6px;
    text-transform: uppercase; color: var(--brand-blue);
  }

  .person { position: absolute; right: 28px; top: 34px; text-align: right; }
  .person__name { font-weight: 900; font-size: 20px; color: var(--brand-blue); text-transform: uppercase; letter-spacing: -.2px; }
  .person__title { font-size: 13px; color: var(--text-light); margin-top: 2px; }

  .divider { position: absolute; left: 30px; right: 28px; top: 152px; height: 1px; background: var(--edge); }

  .address { position: absolute; right: 28px; top: 166px; text-align: right; font-size: 13px; line-height: 1.4; color: var(--text-light); }

  .contacts { position: absolute; left: 30px; top: 166px; list-style: none; font-size: 13px; line-height: 1.55; color: var(--text-light); }
  .contacts li { display: flex; align-items: center; gap: 7px; }
  .contacts svg { width: 11px; height: 11px; flex: none; }

  .back__pattern {
    position: absolute; inset: 0;
    background: linear-gradient(135deg, #0d0d0d 0%, #1a1a1a 55%, #2a2a2a 100%);
  }
  .back__brand { position: absolute; right: 50px; top: 128px; display: flex; align-items: center; gap: 10px; }
</style>
</head>
<body>

<section class="card card--front">
  <div class="brand">
    <span class="brand__square"></span>
    <span class="brand__name">Orrin Wellness Group</span>
  </div>
  <p class="brand__tagline">Dedicated to hope, healing and recovery</p>

  <div class="person">
    <p class="person__name">Daniel Corvane</p>
    <p class="person__title">President</p>
  </div>

  <div class="divider"></div>

  <ul class="contacts">
    <li>
      <svg viewBox="0 0 12 12"><path d="M3 1l2 2.5-1.2 1.2a6 6 0 0 0 3.5 3.5L8.5 7 11 9l-1.3 1.8C5.5 10.5 1.5 6.5 1.2 2.3z" fill="var(--brand-orange)"/></svg>
      555-014-2287
    </li>
    <li>
      <svg viewBox="0 0 12 12"><rect x="1" y="2.5" width="10" height="7" fill="var(--brand-green)"/><path d="M1 2.5l5 4 5-4" fill="none" stroke="var(--card)" stroke-width="1"/></svg>
      info@orrinwellness.com
    </li>
    <li>
      <svg viewBox="0 0 12 12"><circle cx="6" cy="6" r="5" fill="var(--brand-purple)"/><path d="M1 6h10M6 1c2 2.5 2 7.5 0 10M6 1c-2 2.5-2 7.5 0 10" fill="none" stroke="var(--card)" stroke-width=".8"/></svg>
      www.orrinwellness.com
    </li>
  </ul>

  <p class="address">1180 Marlow Cove Drive<br>Seabright CA 90210</p>
</section>

<section class="card card--back">
  <div class="back__pattern" role="img" aria-label="Tone-on-tone repeating brand mark pattern in dark gloss"></div>
  <div class="back__brand">
    <span class="brand__square"></span>
    <span class="brand__name">Orrin Wellness Group</span>
  </div>
</section>

</body>
</html>
```